Professional Services - letterhead / business cards

The company (velmora partners) will provide services to Investment Funds and large investors in Spain. I have recently chosen a logo that I am attaching.

I would like a simple stationary design that i could use as letter head, business cards and "with compliments" cards.

I am not quite sure which color I will mostly use for the logo, in the email signature I will probably lean towards the white background and grey letters. I am attaching my favourite options.

Target Market(s)

Large Multinationals, Investment funds and Law firms

Industry/Entity Type

Business

Requirements
Must have
• my details are:
Luis R. Abadal
Velmora Partners S.L.
Casa de Torrelumbre
Calle de Vientoalto 27
28014 Madrid
T: +34 (91) 387-2265
M: +34 (646) 819-054
e-mail: labadal@velmorapartners.com

```html
<!DOCTYPE html>
<html lang="en">
<head>
<meta charset="utf-8">
<title>Velmora Partners – Business Card</title>
<link rel="stylesheet" href="https://fonts.googleapis.com/css2?family=Jost:wght@300;400;500&display=swap">
<style>
  :root {
    --navy: #0c1377;
    --navy-deep: #080e5e;
    --paper: #ffffff;
    --ink-grey: #6e6e70;
    --badge-grey: #b9b9bb;
    --backdrop: #e8e6e2;
  }
  * { box-sizing: border-box; margin: 0; padding: 0; }
  html, body {
    width: 1200px;
    height: 588px;
    overflow: hidden;
    background: var(--backdrop);
    font-family: "Jost", "Futura", sans-serif;
  }
  .sheet {
    position: relative;
    width: 1200px;
    height: 588px;
  }
  .card {
    position: absolute;
    top: 144px;
    width: 470px;
    height: 300px;
    border-radius: 16px;
    box-shadow: 0 6px 18px rgba(0,0,0,0.12);
  }
  /* Front side */
  .card--front {
    left: 95px;
    background: var(--navy);
    color: var(--paper);
    display: flex;
    flex-direction: column;
    align-items: center;
    justify-content: center;
  }
  .card--front .wordmark {
    font-size: 40px;
    font-weight: 300;
    letter-spacing: 0.5px;
  }
  .card--front .website {
    margin-top: 22px;
    font-size: 12px;
    font-weight: 400;
    letter-spacing: 3.4px;
  }
  /* Back side */
  .card--back {
    left: 635px;
    background: var(--paper);
    color: var(--ink-grey);
    padding: 38px 36px 0 36px;
  }
  .card--back .wordmark {
    color: var(--navy);
    font-size: 36px;
    font-weight: 300;
    text-align: center;
  }
  .details {
    margin-top: 46px;
    text-align: center;
  }
  .person {
    font-size: 13px;
    font-weight: 400;
  }
  .person__name {
    color: var(--navy);
    font-size: 17px;
    letter-spacing: 1px;
    text-transform: uppercase;
  }
  .email {
    margin-top: 2px;
    font-size: 12px;
  }
  .email__domain { color: var(--navy); }
  .phones {
    margin-top: 10px;
    display: flex;
    justify-content: center;
    gap: 22px;
    font-size: 13px;
  }
  .phone {
    display: inline-flex;
    align-items: center;
    gap: 8px;
  }
  .phone__badge {
    display: inline-flex;
    align-items: center;
    justify-content: center;
    width: 15px;
    height: 15px;
    border-radius: 50%;
    background: var(--badge-grey);
    color: var(--paper);
    font-size: 9px;
    font-weight: 500;
  }
  .address {
    margin-top: 6px;
    font-size: 12.5px;
  }
</style>
</head>
<body>
<main class="sheet">
  <section class="card card--front" aria-label="Business card front">
    <div class="wordmark">velmora partners</div>
    <div class="website">www.velmorapartners.com</div>
  </section>

  <section class="card card--back" aria-label="Business card back">
    <div class="wordmark">velmora partners</div>
    <div class="details">
      <p class="person"><span class="person__name">Luis R. Abadal,</span> Velmora Partners S.L.</p>
      <p class="email">labadal@<span class="email__domain">velmorapartners</span>.com</p>
      <div class="phones">
        <span class="phone"><span class="phone__badge">P</span>+34 (91) 387-2265</span>
        <span class="phone"><span class="phone__badge">C</span>+34 (646) 819-054</span>
      </div>
      <p class="address">Casa de Torrelumbre, Calle de Vientoalto 27, 28014 Madrid</p>
    </div>
  </section>
</main>
</body>
</html>
```